AMBER AND SLATE WEB

We need a home design in wordpress, we have now a web but we would like to improve it. Our current web is www.amberandslatevillas.example Our business is holliday rental of villas in Ibiza. Our guest must know that we are a reliable company, professional and with experience and good reviews. We want them to click in our reservation engine: https://bookings.amberandslatevillas.example/en/ and make reservation in our website. We would also like to say that all the properties that we have are just us who commercialize so we have best price available. Many people are going to see our villas in staylist.example and look to our website to make a reservation with us so we need to show them that they are at the right place and click at our link to our reservation engine. What make us special is that we are a local company, we are from Ibiza, Our guests are always received in person by the Amber and Slate Ibiza team. You will enjoy extensive tourist information when you check in and during the entire stay. You will be attended by ChatterLine and calls, always happy to help so that you have a happy and fun stay! Our guest stay is better than in hotel as they have more spece, private swiming pool, private garden, barbeque ... To rent a villa is the best way to stay in Ibiza. We also have a promotional video: https://vidshare.example/Qm7TzR2pLxA Let our philosophy be shown, we think that coming on holiday to Ibiza implies seeing the nature that we have in Ibiza, hence our name AMBER AND SLATE, like the pins that almost touch the sea in Ibiza, or the posidonea meadows where the intense green of the seaweed and the blue of the sea. We are aware of the environment, and we love Ibiza. For us, the client who visits Ibiza, should rent a car, go around the island, eat in a restaurant one day in front of the sea, is a night of partying to the discs, go shopping, visit the ancient heritage of Umanity, make some aquatic sport, enjoy the pool, those are for us Ibiza.

Target Market(s)

Europe, people from Holand, UK, Germany, France, Spain ...

Industry/Entity Type

Tourism

Colors

Designer to choose colors to be used in the design.

Requirements
Must have
• Pictures of Ibiza.
Nice to have
• Our name Amber and Slate Ibiza is beacuse in Ibiza there is forest that almost touch the watter of the Mediterranean sea, so you can see green of the forest and blue of the sea and the sky. And also beacause under the watter of the sea there is a plant called Posidonia that is also green please see the picture of posidonia.

```html
<!DOCTYPE html>
<html lang="en">
<head>
<meta charset="utf-8">
<title>Amber and Slate Ibiza – Villas</title>
<link href="https://fonts.googleapis.com/css2?family=Cinzel:wght@400;600;700&family=Marcellus&family=Jost:wght@400;500;600&display=swap" rel="stylesheet">
<style>
:root{
  --green:#5d7a2c;
  --green-dark:#4b6522;
  --green-light:#8cc63f;
  --blue:#2f8fd8;
  --blue-deep:#1f6fb8;
  --teal-title:#2a86c0;
  --ink:#333;
  --muted:#666;
  --line:#e4e4e4;
  --grey-bg:#f4f4f4;
  --white:#fff;
  --star:#f2a81d;
}
*{box-sizing:border-box;margin:0;padding:0}
html,body{width:1200px;height:4592px;overflow:hidden}
body{font-family:"Jost",sans-serif;color:var(--ink);background:var(--white);position:relative}
.abs{position:absolute}
.title{font-family:"Cinzel",serif;font-weight:600;font-size:32px;text-align:center;color:var(--green);letter-spacing:1px}
.title span{color:var(--teal-title)}
.btn{display:inline-flex;align-items:center;justify-content:center;font-family:"Cinzel",serif;font-size:14px;color:#fff;background:var(--green);letter-spacing:1px;white-space:nowrap}
.ph{display:block}

/* header */
.topline{left:0;top:0;width:1200px;height:6px;background:linear-gradient(90deg,var(--green-light),var(--blue))}
.header{left:0;top:6px;width:1200px;height:101px;background:#fff}
.brand{display:flex;align-items:center;gap:10px;font-family:"Marcellus",serif;font-size:22px;color:var(--green);white-space:nowrap}
.brand i{width:22px;height:22px;border-radius:50%;background:var(--green);display:block}
.nav{left:414px;display:flex;gap:26px;font-size:14px;font-family:"Marcellus",serif;color:var(--ink);white-space:nowrap}
.nav .active{color:var(--green);border-bottom:2px solid var(--green);padding-bottom:3px}
.flag{left:1088px;width:26px;height:15px;background:linear-gradient(#c33 0 50%,#eee 50%);border:1px solid #ccc}

/* hero */
.hero{left:0;top:107px;width:1200px;height:496px;background:linear-gradient(160deg,#3d7a4d 0%,#5a9a6a 35%,#2f9cc0 70%,#2a6f4a 100%)}
.hero-title{left:0;top:262px;width:1200px;text-align:center;font-family:"Marcellus",serif;font-size:52px;line-height:62px;color:#fff;text-shadow:0 2px 6px rgba(0,0,0,.35);font-weight:400}

.booking{left:141px;top:563px;width:918px;height:95px;background:#fff;box-shadow:0 6px 20px rgba(0,0,0,.15);display:flex;align-items:flex-start;padding:14px 22px;gap:16px;font-size:12px}
.field label{display:block;margin-bottom:6px;color:var(--ink);white-space:nowrap}
.field .box{height:36px;border:1px solid var(--line);display:flex;align-items:center;padding:0 10px;gap:8px;color:#888;font-size:11px;white-space:nowrap}
.field .box b{width:13px;height:12px;border:2px solid var(--blue);border-radius:2px;display:block}

/* about */
.about-title{left:141px;top:768px;display:flex;align-items:center;gap:14px;font-family:"Cinzel",serif;font-size:30px;color:var(--green)}
.about-text{left:141px;top:840px;width:625px;font-size:13px;line-height:20px;color:var(--muted)}
.about-text p{margin-bottom:14px}
.about-shape{left:820px;top:728px;width:190px;height:312px;border-radius:50% 50% 45% 45%/40% 40% 55% 55%;background:linear-gradient(180deg,#6fc7e8,#1f88c8 55%,#d9cfa8)}

/* amenities */
.amenities{left:0;top:1193px;width:1200px;height:591px;background:var(--grey-bg)}
.amen-photo{left:141px;top:1337px;width:428px;height:361px;background:linear-gradient(160deg,#4a8fd6,#dfe8ee 55%,#7e8c5a)}
.amen-panel{left:569px;top:1337px;width:490px;height:306px;background:#fff;display:grid;grid-template-columns:200px 1fr;column-gap:14px;padding:30px 20px}
.amen-item{display:flex;align-items:center;gap:10px;font-size:13px;border-bottom:1px solid var(--line);height:62px;white-space:nowrap}
.amen-item svg{flex:none}
.amen-btn{left:569px;top:1643px;width:490px;height:55px;font-size:17px}

/* video */
.videoband{left:0;top:1784px;width:1200px;height:395px;background:linear-gradient(180deg,#3b3a36,#5a5f58 60%,#2e3b44)}
.video-sub{left:360px;top:1908px;width:480px;text-align:center;color:#fff;font-size:12px;line-height:18px}
.video-frame{left:291px;top:1989px;width:618px;height:376px;background:#fff;padding:8px;box-shadow:0 6px 18px rgba(0,0,0,.25)}
.video-inner{width:100%;height:100%;background:linear-gradient(180deg,#2f7fc9,#e6e1d6 55%,#3e9ccf 85%);position:relative}
.play{left:274px;top:152px;width:56px;height:56px;border:3px solid #fff;border-radius:50%}
.arrow{width:46px;height:46px;background:var(--blue);display:flex;align-items:center;justify-content:center}

/* gallery */
.gallery{left:141px;top:2512px;width:918px;display:grid;grid-template-columns:repeat(4,1fr);grid-template-rows:205px 205px;gap:8px}
.gallery .ph{width:100%;height:100%}
.g-over{background:rgba(47,143,216,.88);color:#fff;display:flex;flex-direction:column;align-items:center;justify-content:center;text-align:center;font-size:14px;padding:0 30px;gap:10px}

/* cta */
.cta{left:0;top:3078px;width:1200px;height:251px;background:linear-gradient(180deg,#2b4e6a,#1f5672 60%,#1d3d4a)}
.cta-title{left:0;top:3140px;width:1200px;text-align:center;font-family:"Cinzel",serif;font-size:30px;line-height:40px;color:#fff;letter-spacing:1px}

/* testimonials */
.t-card{background:#fff;text-align:center;font-size:12px;line-height:18px;color:var(--muted);padding:34px 40px}
.t-side{opacity:.35}
.t-main{box-shadow:0 4px 20px rgba(0,0,0,.12)}
.stars{color:var(--star);font-size:16px;letter-spacing:2px;margin-top:10px}
.avatar{left:561px;top:3762px;width:78px;height:78px;border-radius:50%;background:linear-gradient(#b9a48f,#6d5a4a);border:3px solid #fff;box-shadow:0 2px 8px rgba(0,0,0,.2)}

/* newsletter */
.news{left:0;top:3947px;width:1200px;height:343px;background:linear-gradient(100deg,#1d6fc0 0%,#2e8fd0 45%,#6bbf4a 85%,#8cc63f 100%)}
.news-title{left:141px;top:4023px;font-family:"Cinzel",serif;font-size:30px;color:#fff}
.news-text{left:141px;top:4070px;width:430px;color:#fff;font-size:13px;line-height:20px}
.news-input{left:141px;top:4148px;width:276px;height:40px;background:#fff;font-size:11px;color:#999;padding:0 12px;display:flex;align-items:center}
.news-btn{left:428px;top:4148px;width:154px;height:40px}
.news-art{left:600px;top:4010px;width:480px;height:280px;background:linear-gradient(180deg,rgba(255,255,255,0) 0%,rgba(240,205,70,.35) 100%)}

/* footer */
.footer{left:0;top:4290px;width:1200px;height:260px;background:var(--grey-bg)}
.f-h{font-family:"Cinzel",serif;font-size:13px;font-weight:600;color:var(--ink);margin-bottom:14px}
.f-list{list-style:none;font-size:12px;line-height:26px;color:var(--muted)}
.f-list li::before{content:"›";margin-right:6px;color:var(--green)}
.contact{font-size:12px;line-height:18px;color:var(--muted)}
.contact div{display:flex;gap:8px;margin-bottom:10px}
.map{left:577px;top:4352px;width:212px;height:108px;background:linear-gradient(135deg,#e8ece4,#d6e2cf 50%,#cfe0ee)}
.socials{left:898px;top:4428px;display:flex;gap:6px}
.socials span{width:20px;height:20px;background:var(--blue-deep);display:block}
.copy{left:0;top:4550px;width:1200px;height:42px;background:var(--green);color:#fff;font-size:12px;display:flex;align-items:center;justify-content:center}
</style>
</head>
<body>

<div class="abs topline"></div>
<header class="abs header">
  <div class="abs brand" style="left:66px;top:34px"><i></i>Amber and Slate</div>
  <nav class="abs nav" style="top:48px"><span class="active">Home</span><span>Experience</span><span>About us</span><span>Contact Us</span></nav>
  <span class="abs btn" style="left:788px;top:40px;width:142px;height:36px;background:var(--blue);font-size:13px">All Properties</span>
  <span class="abs btn" style="left:950px;top:40px;width:116px;height:36px;font-size:13px">Book Now</span>
  <span class="abs flag" style="top:50px"></span>
</header>

<section class="abs hero" role="img" aria-label="Villa terrace with swimming pool and palm trees in Ibiza"></section>
<h1 class="abs hero-title">The Best Way To Stay<br>In Ibiza!</h1>

<form class="abs booking">
  <div class="field" style="width:260px"><label>Check-in and check-out date:</label><div class="box"><b></b>Select dates for your stay</div></div>
  <div class="field" style="width:70px"><label>Nights:</label><div class="box" style="justify-content:center">1</div></div>
  <div class="field" style="width:190px"><label>No. of guests and rooms:</label><div class="box"><b></b>2 adults (1 room)</div></div>
  <div class="field" style="width:160px"><label>Promo Code:</label><div class="box"><b></b>Promo</div></div>
  <div class="field" style="width:124px"><label>&nbsp;</label><span class="btn" style="width:124px;height:36px">Search</span></div>
</form>

<div class="abs about-title">About <span class="brand" style="font-size:22px"><i></i>Amber and Slate</span></div>
<div class="abs about-text">
  <p>Amber and Slate Villas Ibiza is a company specialized in offering its clients accommodation in villas on the countryside of Ibiza. Our guests enjoy the rural Ibiza, tranquility, relax, private pool, close to dream beaches and coves, the best restaurants, an unforgettable holiday for family or friends.</p>
  <p>Every day can be a different experience, beach, restaurant, flea market, disco, hiking, kayaking, horseback riding, shopping, history, boat ride! There is a lot of variety for all budgets!</p>
  <p>The maximum distances of the island are 41 kilometers from north to south and 15 kilometers from east to west, we always recommend renting a car. Enjoy the freedom to go where you prefer, without depending on schedules or public transportation.</p>
</div>
<span class="abs btn" style="left:141px;top:1059px;width:122px;height:34px;font-size:12px">Read More</span>
<div class="abs about-shape" role="img" aria-label="Tree-shaped photo of an Ibiza cove with turquoise water"></div>

<section class="abs amenities"></section>
<h2 class="abs title" style="left:0;top:1268px;width:1200px">Our <span>Amenities</span></h2>
<div class="abs amen-photo" role="img" aria-label="Sun loungers beside a villa pool under blue sky"></div>
<div class="abs amen-panel">
  <div class="amen-item"><svg width="22" height="22" viewBox="0 0 22 22" fill="none" stroke="#2f8fd8" stroke-width="1.6"><rect x="3" y="8" width="16" height="8" rx="2"/><circle cx="7" cy="17" r="2"/><circle cx="15" cy="17" r="2"/></svg>Rent A Car</div>
  <div class="amen-item"><svg width="22" height="22" viewBox="0 0 22 22" fill="none" stroke="#2f8fd8" stroke-width="1.6"><path d="M11 3v16M5 19h12M4 8c3-4 11-4 14 0"/></svg>Go Around The Island</div>
  <div class="amen-item"><svg width="22" height="22" viewBox="0 0 22 22" fill="none" stroke="#2f8fd8" stroke-width="1.6"><path d="M4 7h14l-1 12H5z"/><path d="M8 7a3 3 0 016 0"/></svg>Go Shopping</div>
  <div class="amen-item"><svg width="22" height="22" viewBox="0 0 22 22" fill="none" stroke="#2f8fd8" stroke-width="1.6"><path d="M6 3v16M4 3v5h4V3M15 3c-2 2-2 6 0 7v9"/></svg>Eat In A Restaurant</div>
  <div class="amen-item"><svg width="22" height="22" viewBox="0 0 22 22" fill="none" stroke="#2f8fd8" stroke-width="1.6"><path d="M2 15c3-2 5 2 9 0s6 2 9 0M6 12l5-8 5 8"/></svg>Aquatic Sport</div>
  <div class="amen-item"><svg width="22" height="22" viewBox="0 0 22 22" fill="none" stroke="#2f8fd8" stroke-width="1.6"><path d="M4 4h14l-7 8zM11 12v7M7 19h8"/></svg>Night Of Partying To The Discos</div>
  <div class="amen-item" style="border:0"><svg width="22" height="22" viewBox="0 0 22 22" fill="none" stroke="#2f8fd8" stroke-width="1.6"><path d="M3 12h16M3 16c3-2 5 2 8 0s5 2 8 0M7 12V4h8"/></svg>Enjoy The Pool</div>
  <div class="amen-item" style="border:0"><svg width="22" height="22" viewBox="0 0 22 22" fill="none" stroke="#2f8fd8" stroke-width="1.6"><path d="M3 19h16M5 19V9M11 19V9M17 19V9M3 9l8-5 8 5z"/></svg>Visit The Ancient Heritage Of Humanity</div>
</div>
<span class="abs btn amen-btn">Book Now</span>

<section class="abs videoband" role="img" aria-label="Dim view of a villa pool at dusk"></section>
<h2 class="abs title" style="left:0;top:1862px;width:1200px;color:#fff">Watch Videos</h2>
<p class="abs video-sub">Lorem ipsum dolor sit amet, consectetuer adipiscing elit, sed diam nonummy nibh euismod tincidunt ut laoreet dolore magna aliquam erat volutpat modo consequat.</p>
<div class="abs video-frame">
  <div class="video-inner" role="img" aria-label="White Ibiza villa with pool, video preview">
    <div class="abs play"><svg width="50" height="50" viewBox="0 0 50 50" style="display:block"><path d="M20 15l15 10-15 10z" fill="#fff"/></svg></div>
  </div>
</div>
<div class="abs arrow" style="left:245px;top:2155px"><svg width="14" height="14" viewBox="0 0 14 14"><path d="M9 2L4 7l5 5" stroke="#fff" stroke-width="2" fill="none"/></svg></div>
<div class="abs arrow" style="left:909px;top:2155px"><svg width="14" height="14" viewBox="0 0 14 14"><path d="M5 2l5 5-5 5" stroke="#fff" stroke-width="2" fill="none"/></svg></div>

<h2 class="abs title" style="left:0;top:2443px;width:1200px">Our <span>Gallery</span></h2>
<div class="abs gallery">
  <div class="ph" role="img" aria-label="White villa among pine trees" style="background:linear-gradient(160deg,#4e93d6,#e9e2d2 50%,#5f7f38)"></div>
  <div class="ph" role="img" aria-label="Pool surrounded by garden" style="background:linear-gradient(160deg,#4a7d3a,#4fa9d8 60%,#c9c1a8)"></div>
  <div class="g-over"><svg width="34" height="34" viewBox="0 0 34 34" fill="none" stroke="#fff" stroke-width="2"><circle cx="17" cy="17" r="15"/><path d="M17 10v14M10 17h14"/></svg>Lorem ipsum dolor sit amet consectetuer<span style="width:6px;height:6px;border-radius:50%;background:#fff"></span></div>
  <div class="ph" role="img" aria-label="Villa living room interior" style="background:linear-gradient(160deg,#d9c9ad,#8a6b4c 60%,#5b6b7a)"></div>
  <div class="ph" role="img" aria-label="Shaded terrace with dining table" style="background:linear-gradient(160deg,#8b6a45,#d8c39e 55%,#6b5a45)"></div>
  <div class="ph" role="img" aria-label="Villa and pool in the afternoon" style="background:linear-gradient(160deg,#3d8fd6,#e3d6b8 45%,#2f9bd0)"></div>
  <div class="ph" role="img" aria-label="Large turquoise pool with lawn" style="background:linear-gradient(160deg,#6fa2d8,#5f8a3d 40%,#35b2e0)"></div>
  <div class="ph" role="img" aria-label="Villa garden with pool and palms" style="background:linear-gradient(160deg,#3b8ad6,#b56d4d 45%,#3fa9d9)"></div>
</div>
<span class="abs btn" style="left:541px;top:2955px;width:118px;height:36px;font-size:12px">View More</span>

<section class="abs cta" role="img" aria-label="Boats anchored in an Ibiza bay at dusk"></section>
<h2 class="abs cta-title">Villas And The Countryside<br>The Best Option To Stay In Ibiza</h2>
<span class="abs btn" style="left:516px;top:3242px;width:168px;height:42px">Book Now</span>

<h2 class="abs title" style="left:0;top:3441px;width:1200px">Client <span>Testimonials</span></h2>
<div class="abs t-card t-side" style="left:184px;top:3510px;width:240px;height:210px">Lorem ipsum dolor sit amet, consectetuer adipiscing elit, sed diam nonummy nibh euismod tincidunt ut laoreet dolore magna aliquam erat volutpat. Ut wisi enim ad minim veniam.<div class="stars">★★★★★</div></div>
<div class="abs t-card t-side" style="left:776px;top:3510px;width:240px;height:210px">Lorem ipsum dolor sit amet, consectetuer adipiscing elit, sed diam nonummy nibh euismod tincidunt ut laoreet dolore magna aliquam erat volutpat. Ut wisi enim ad minim veniam.<div class="stars">★★★★★</div></div>
<div class="abs t-card t-main" style="left:416px;top:3488px;width:368px;height:245px"><svg width="30" height="24" viewBox="0 0 30 24" style="position:absolute;left:18px;top:16px"><path d="M2 22V12C2 6 6 2 12 2v4c-3 0-5 2-5 6h5v10zM17 22V12c0-6 4-10 10-10v4c-3 0-5 2-5 6h5v10z" fill="#ccc"/></svg>Lorem ipsum dolor sit amet, consectetuer adipiscing elit, sed diam nonummy nibh euismod tincidunt ut laoreet dolore magna aliquam erat volutpat. Ut wisi enim ad minim veniam, quis nostrud exerci tation ullamcorper suscipit.<div class="stars">★★★★★</div></div>
<div class="abs avatar" role="img" aria-label="Guest portrait"></div>
<div class="abs" style="left:0;top:3852px;width:1200px;text-align:center;font-family:'Cinzel',serif;font-size:14px;color:var(--muted)">Marco Ferrer</div>

<section class="abs news"></section>
<h2 class="abs news-title">Newsletter Sign Up</h2>
<p class="abs news-text">Lorem ipsum dolor sit amet, consectetuer adipiscing elit, sed diam nonummy nibh euismod tincidunt ut laoreet dolore magna aliquam erat volutpat modo consequat.</p>
<div class="abs news-input">Enter your Email Address</div>
<span class="abs btn news-btn">Subscribe</span>
<div class="abs news-art" role="img" aria-label="Travel illustration of an airplane over a sunny sky"></div>

<footer class="abs footer"></footer>
<div class="abs" style="left:141px;top:4330px">
  <div class="f-h">Quick Links</div>
  <ul class="f-list"><li>Home</li><li>Experience</li><li>About us</li><li>Contact Us</li></ul>
</div>
<div class="abs contact" style="left:291px;top:4330px;width:260px">
  <div class="f-h">Contact Details</div>
  <div><svg width="12" height="14" viewBox="0 0 12 14"><path d="M6 1a4.5 4.5 0 00-4.5 4.5C1.5 9 6 13 6 13s4.5-4 4.5-7.5A4.5 4.5 0 006 1z" fill="#555"/><circle cx="6" cy="5.5" r="1.6" fill="#fff"/></svg><span><b style="font-family:Cinzel,serif;color:var(--ink)">Amber &amp; Slate</b><br>123 Lorem ipsum dolor sit amet,<br>consectetuer adipiscing elit</span></div>
  <div><svg width="12" height="14" viewBox="0 0 12 14"><path d="M3 1l2 3-1.5 1.5c.7 1.6 2 3 3.5 3.5L8.5 7.5l3 2-1 2.5C6 12 1 7 1.5 2z" fill="#555"/></svg>+34 600 000 111</div>
  <div><svg width="12" height="14" viewBox="0 0 12 14"><rect x="1" y="3" width="10" height="8" fill="none" stroke="#555"/><path d="M1 3l5 4 5-4" fill="none" stroke="#555"/></svg><span style="font-size:11px">reservas@amberandslatevillas.example</span></div>
</div>
<div class="abs f-h" style="left:577px;top:4330px">Location Map</div>
<div class="abs map" role="img" aria-label="Small location map of the office"></div>
<div class="abs brand" style="left:860px;top:4380px;font-size:20px"><i></i>Amber and Slate</div>
<div class="abs socials"><span></span><span></span><span></span><span></span></div>
<div class="abs copy">Copyright © 2019 Amber &amp; Slate. All Rights Reserved.</div>

</body>
</html>
```